Security company needs a business card design

We have a logo & we provide security services specialising in the construction site industry & remote areas. We are looking for a modern design preferably hi-tech as we provide hi-end specialised security services. We do not do pubs, clubs etc. Many of our employees are ex defence force & are highly qualified in covert ops etc.

Below are details that we would like on the front of the business card (I have attached our logo)
Logo + ML 738204195 (ML is abbreviation for "Master License")
We are also members of "GRTOV" not sure if we need to put their logo on the business card or just make a reference to our membership (please advise - I have also attached their logo)

Company name: Bluegate Security Services Pty Ltd

1) Employee name: Darren Kowalczyk
Designation: Security Advisor / Director
Contact: M: 0431 582 907
e:darren@bluegatesecurityservices.com.au (500cards 1st order)
2) Employee name: Trevor Kowalczyk
Designation: Manager
Contact: M: 0476 213 564
e:trevor@bluegatesecurityservices.com.au (250cards 1st order)
3) a generic card with no employee name or designation (250cards 1st order)

Company Address: 316 Wattlebrook Rd, Marlow Creek NSW 2457
T: +61 2 6610 4932 F: +61 2 6610 4958
E:admin@bluegatesecurityservices.com.au
www.bluegatesecurityservices.com.au

Below are details we provide which have been placed previously on the back of our business card:
Static Guards; Mobile Vehicle patrols; Alarm monitoring; 3 G CCTV Monitoring; Specialists in providing security requirements for construction sites & remote areas.
Updates

                                        Refer new pdf just uploaded

Target Market(s)

Security required for construction sites & remote areas

Industry/Entity Type

Construction

```html
<!DOCTYPE html>
<html lang="en">
<head>
<meta charset="utf-8">
<title>Bluegate Security Services – Business Card</title>
<link rel="stylesheet" href="https://fonts.googleapis.com/css2?family=Arimo:wght@400;700&display=swap">
<style>
  :root {
    --bg-top: #d4d4d6;
    --bg-bottom: #a9a9ac;
    --card-light: #ffffff;
    --card-silver: #dcdee0;
    --navy: #1c1a86;
    --navy-deep: #0e0d5a;
    --red: #a5121a;
    --red-deep: #5e0a0e;
    --grey-band: #b9c0c4;
    --ink: #1f1f24;
    --name-blue: #3b35b4;
    --label-red: #d6262c;
    --label-blue: #2a2aa8;
  }
  * { box-sizing: border-box; margin: 0; padding: 0; }
  html, body { width: 1200px; height: 861px; overflow: hidden; }
  body {
    background: linear-gradient(180deg, var(--bg-top), var(--bg-bottom));
    font-family: "Arimo", Arial, sans-serif;
    color: var(--ink);
    display: flex;
    align-items: center;
    justify-content: center;
    gap: 50px;
  }
  .card {
    position: relative;
    width: 520px;
    height: 318px;
    background: linear-gradient(150deg, var(--card-light) 30%, var(--card-silver));
    box-shadow: 0 10px 24px rgba(0,0,0,.28);
    overflow: hidden;
  }
  .card__bands { position: absolute; inset: 0; width: 100%; height: 100%; }
  .brand {
    position: absolute;
    display: flex;
    align-items: center;
    gap: 8px;
    font-weight: 700;
    color: var(--navy);
  }
  .brand__dot {
    width: 14px; height: 14px;
    border-radius: 50%;
    background: var(--navy);
  }
  .card--front .brand { top: 34px; right: 30px; font-size: 15px; }
  .holder { position: absolute; left: 28px; top: 78px; }
  .holder__name { font-size: 24px; line-height: 28px; font-weight: 700; color: var(--name-blue); }
  .holder__role { font-size: 12.5px; line-height: 15px; font-weight: 700; }
  .contacts { margin-top: 6px; font-size: 11px; line-height: 14px; }
  .contacts__group + .contacts__group { margin-top: 4px; }
  .contacts__row { display: flex; gap: 10px; }
  .contacts__label { width: 10px; font-weight: 700; }
  .contacts__label--red { color: var(--label-red); }
  .contacts__label--blue { color: var(--label-blue); }
  .license { position: absolute; top: 58px; right: 30px; font-size: 10px; color: var(--navy); }

  .card--back .brand {
    top: 118px; left: 0; right: 0;
    justify-content: center;
    font-size: 22px;
  }
  .card--back .brand__dot { width: 20px; height: 20px; }
  .services {
    position: absolute;
    left: 28px; bottom: 26px;
    font-size: 11.5px;
    line-height: 15px;
  }
</style>
</head>
<body>

  <article class="card card--front">
    <svg class="card__bands" viewBox="0 0 520 318" preserveAspectRatio="none" aria-hidden="true">
      <polygon points="0,275 520,205 520,232 0,298" fill="var(--grey-band)" opacity=".8"/>
      <polygon points="170,318 520,232 520,280 390,318" fill="var(--navy)"/>
      <polygon points="0,298 400,240 170,318 0,318" fill="var(--red)"/>
      <polygon points="0,310 230,275 170,318 0,318" fill="var(--red-deep)"/>
    </svg>
    <div class="brand"><span class="brand__dot"></span>Bluegate Security Services</div>
    <p class="license">ML 738204195</p>
    <section class="holder">
      <h1 class="holder__name">Darren Kowalczyk</h1>
      <p class="holder__role">Security Advisor / Director</p>
      <div class="contacts">
        <div class="contacts__group">
          <p class="contacts__row"><span class="contacts__label contacts__label--red">M</span>0431 582 907</p>
          <p class="contacts__row"><span class="contacts__label contacts__label--red">E</span>darren@bluegatesecurityservices.com.au</p>
        </div>
        <div class="contacts__group">
          <p class="contacts__row"><span class="contacts__label contacts__label--blue">A</span>316 Wattlebrook Rd, Marlow Creek NSW 2457</p>
          <p class="contacts__row"><span class="contacts__label contacts__label--blue">T</span>+61 2 6610 4932</p>
          <p class="contacts__row"><span class="contacts__label contacts__label--blue">F</span>+61 2 6610 4958</p>
          <p class="contacts__row"><span class="contacts__label contacts__label--blue">E</span>admin@bluegatesecurityservices.com.au</p>
          <p class="contacts__row"><span class="contacts__label contacts__label--blue">W</span>www.bluegatesecurityservices.com.au</p>
        </div>
      </div>
    </section>
  </article>

  <article class="card card--back">
    <svg class="card__bands" viewBox="0 0 520 318" preserveAspectRatio="none" aria-hidden="true">
      <polygon points="0,0 520,0 520,28 0,120" fill="var(--grey-band)" opacity=".8"/>
      <polygon points="0,0 330,0 0,95" fill="var(--navy)"/>
      <polygon points="200,0 520,0 520,30 130,65" fill="var(--red)"/>
      <polygon points="380,0 520,0 520,22" fill="var(--red-deep)"/>
      <polygon points="0,0 160,0 0,60" fill="var(--navy-deep)"/>
    </svg>
    <div class="brand"><span class="brand__dot"></span>Bluegate Security Services</div>
    <p class="services">
      Static Guards • Mobile Vehicle Patrols • Alarm Monitoring • 3G CCTV Monitoring<br>
      Specialists in providing security requirements for construction sites &amp; remote areas
    </p>
  </article>

</body>
</html>
```